6-seitiges Prospekt für Messer und Fräser für den industriellen Zuschnitt auf CNC-Flachbettanlagen
Zielgruppe
Hergestellt werden Messer und Fräser für den industriellen Zuschnitt auf CNC-Flachbettanlagen.
Den Einsatz dieser sieht man unter anderem hier: https://www.videoportal-beispiel.de/watch?v=QX7mLpR2aZk
Aufgabenstellung
Der Prospekt wird ein 6-Seiter (gefaltet), Seitengröße DIN A4 Hochformat und wird zweisprachig (englisch/deutsch). Er soll edel und modern anmuten.
Von euch hier soll der Titel und eine Produktseite designt werden.
Die beigestellte Datei enthält alle Beschreibungen/Texte und zu die verwendenen Bilder.

```html
<!DOCTYPE html>
<html lang="de">
<head>
<meta charset="utf-8">
<title>KlingWerk – Messer, Fräser und Zubehör</title>
<link rel="stylesheet" href="https://fonts.googleapis.com/css2?family=Lato:ital,wght@0,400;0,700;1,300;1,400&display=swap">
<style>
  :root {
    --backdrop: #dcdcdc;
    --paper: #ffffff;
    --brand-red: #b01f26;
    --steel-dark: #9ca1a5;
    --steel-light: #dfe2e5;
    --steel-bright: #eef0f3;
    --steel-mid: #b4b8bd;
    --band-grey: #cbcbcb;
    --rule-grey: #a1a5a8;
    --text-white: #ffffff;
  }
  * { margin: 0; padding: 0; box-sizing: border-box; }
  html, body { width: 1200px; height: 1200px; overflow: hidden; }
  body { background: var(--backdrop); position: relative; font-family: "Lato", sans-serif; }

  .cover {
    position: absolute; left: 176px; top: 0;
    width: 848px; height: 1200px;
    background: var(--paper);
    overflow: hidden;
  }
  .cover__shapes { position: absolute; inset: 0; }

  .brand {
    position: absolute; left: 528px; top: 76px;
    display: flex; align-items: center; gap: 12px;
  }
  .brand__square { width: 40px; height: 40px; background: var(--brand-red); }
  .brand__name {
    font-family: "Lato", sans-serif; font-weight: 700;
    font-size: 40px; color: var(--brand-red); letter-spacing: 0.5px;
  }

  .made-in {
    position: absolute; left: 520px; top: 201px; width: 328px; height: 26px;
    text-align: center; line-height: 26px;
    font-style: italic; font-weight: 400; font-size: 17px;
    letter-spacing: 2.5px; color: var(--text-white);
  }

  .tagline {
    position: absolute; font-style: italic; font-weight: 300;
    font-size: 38px; line-height: 1; color: var(--text-white); white-space: nowrap;
  }
  .tagline--en { left: 208px; top: 747px; }
  .tagline--de { left: 186px; top: 831px; }

  .web {
    position: absolute; left: 81px; top: 1082px;
    font-weight: 700; font-size: 20px; color: var(--brand-red); letter-spacing: 0.3px;
  }
</style>
</head>
<body>
  <main class="cover">
    <svg class="cover__shapes" width="848" height="1200" viewBox="0 0 848 1200">
      <defs>
        <radialGradient id="steelGlow" cx="0.5" cy="0.55" r="0.6">
          <stop offset="0" stop-color="var(--steel-light)"/>
          <stop offset="1" stop-color="var(--steel-dark)"/>
        </radialGradient>
        <linearGradient id="productTone" x1="0" y1="0" x2="1" y2="1">
          <stop offset="0" stop-color="var(--steel-bright)"/>
          <stop offset="1" stop-color="var(--steel-mid)"/>
        </linearGradient>
        <clipPath id="panelClip">
          <polygon points="181,227 823,227 690,723 48,723"/>
        </clipPath>
      </defs>

      <!-- red label band -->
      <polygon class="made-in-band" points="513,201 848,201 848,227 505,227" fill="var(--brand-red)"/>

      <!-- product panel -->
      <g class="product-panel">
        <polygon points="181,227 823,227 690,723 48,723" fill="url(#steelGlow)"/>

        <g class="product-slots" clip-path="url(#panelClip)">
          <polygon role="img" aria-label="Produktfoto: Schleppmesser aus gebürstetem Stahl"
                   points="202,288 256,288 156,666 102,666" fill="url(#productTone)"/>
          <polygon role="img" aria-label="Produktfoto: Fräser mit Spannut"
                   points="382,278 442,278 334,672 280,672" fill="url(#productTone)"/>
          <polygon role="img" aria-label="Produktfoto: schmales Oszillationsmesser"
                   points="542,290 592,290 498,670 444,670" fill="url(#productTone)"/>
          <polygon role="img" aria-label="Produktfoto: achteckiges Rundmesser mit Mittelloch"
                   points="650,367 790,367 740,598 600,598" fill="url(#productTone)"/>
        </g>

        <line x1="337" y1="227" x2="208" y2="723" stroke="var(--paper)" stroke-width="5"/>
        <line x1="500" y1="227" x2="370" y2="723" stroke="var(--paper)" stroke-width="5"/>
        <line x1="663" y1="227" x2="533" y2="723" stroke="var(--paper)" stroke-width="5"/>
      </g>

      <!-- title bands -->
      <polygon class="accent-block" points="0,723 183,723 140,888 0,888" fill="var(--brand-red)"/>
      <polygon class="title-band" points="192,723 848,723 848,801 171,801" fill="var(--band-grey)"/>
      <polygon class="title-rule" points="171,801 659,801 657,809 169,809" fill="var(--rule-grey)"/>
      <polygon class="title-rule-stub" points="169,809 177,809 171,824 165,824" fill="var(--rule-grey)"/>
      <polygon class="title-band" points="177,809 848,809 846,886 157,886" fill="var(--band-grey)"/>
    </svg>

    <div class="brand">
      <span class="brand__square"></span>
      <span class="brand__name">KlingWerk</span>
    </div>

    <p class="made-in">Made in Germany</p>

    <h1 class="tagline tagline--en">Blades, router bits and accessories</h1>
    <h2 class="tagline tagline--de">Messer, Fräser und Zubehör</h2>

    <p class="web">www.klingwerk.de</p>
  </main>
</body>
</html>
```